need corporate, modern business card created for Consulting Company

I need a slick business card using elements from my website, as well as, integrating my pixelforge-created logo (see files).

The business card needs to be:
1. Corporate and modern
2. Clean and professional

I've included a PSD with the logo/icon that you can use to create it. Feel free to try a metallic finish on the logo, make it bigger/small, underlay it. Whatever you need to do to make my card stand out.

Try a black background, or white background or gray.

The idea is for my card to be memorable as well as professional and corporate.

Target Market(s)

Corporate business in the US and Canada.

Industry/Entity Type

Business

Contact Information for Business Card

Commerce Advancing Methods
Martin Coles, Senior Partner
office: 1 877 555 0143
mobile: 1 519 555 0172
website: http://www.brightvale.example

Requirements
Must have
• Card-related information
• corporate, yet modern
• clean and professional
• incorporate the icon only
• must have an editable form when complete!
Nice to have
• metallic icon might be cool
• try it with white or black

```html
<!DOCTYPE html>
<html lang="en">
<head>
<meta charset="utf-8">
<title>Brightvale Business Card</title>
<link href="https://fonts.googleapis.com/css2?family=Open+Sans:wght@400;600&display=swap" rel="stylesheet">
<style>
  :root {
    --ink: #1b1c1e;
    --paper: #ffffff;
    --brand-blue: #3d7bd0;
    --navy: #1d3568;
    --text-light: #e6e8eb;
    --text-muted: #a9adb3;
    --rule: #55585d;
    --backdrop: #e9eaec;
  }
  * { margin: 0; padding: 0; box-sizing: border-box; }
  html, body { width: 1200px; height: 848px; overflow: hidden; }
  body {
    background: var(--backdrop);
    font-family: "Open Sans", Arial, sans-serif;
    position: relative;
  }
  .card {
    position: absolute;
    left: 280px;
    width: 640px;
    height: 366px;
    border-radius: 18px;
    overflow: hidden;
    background: var(--paper);
    box-shadow: 0 6px 18px rgba(0,0,0,0.18);
  }
  .card-front { top: 38px; }
  .card-back { top: 444px; }
  .card-art { position: absolute; inset: 0; width: 100%; height: 100%; }

  .brand { display: flex; align-items: center; gap: 12px; position: absolute; }
  .brand-mark { width: 34px; height: 34px; background: var(--brand-blue); }
  .brand-name { color: var(--brand-blue); font-weight: 600; letter-spacing: 0.5px; }
  .card-front .brand { left: 50%; top: 50%; transform: translate(-50%, -50%); }
  .card-front .brand-name { font-size: 58px; }

  .card-back .brand { left: 40px; top: 118px; gap: 8px; }
  .card-back .brand-mark { width: 18px; height: 18px; }
  .card-back .brand-name { font-size: 28px; }
  .tagline {
    position: absolute; left: 40px; top: 162px;
    color: var(--text-light); font-size: 13px; letter-spacing: 0.3px;
  }
  .tagline-rule { position: absolute; left: 40px; top: 188px; width: 230px; height: 1px; background: var(--rule); }

  .contact { position: absolute; left: 330px; top: 58px; width: 270px; color: var(--text-light); }
  .contact-name { color: var(--brand-blue); font-size: 20px; font-weight: 600; line-height: 1.1; }
  .contact-role { font-size: 10px; color: var(--text-muted); margin-bottom: 10px; }
  .contact-address { font-size: 11.5px; line-height: 1.45; }
  .contact-rule { height: 1px; background: var(--rule); margin: 10px 0; }
  .contact-list { list-style: none; }
  .contact-list li { display: flex; align-items: center; gap: 12px; font-size: 12px; height: 23px; }
  .contact-icon { width: 18px; height: 18px; flex: none; }
</style>
</head>
<body>

<section class="card card-front" aria-label="Card front">
  <svg class="card-art" viewBox="0 0 640 366" aria-hidden="true">
    <g class="stripe-pair">
      <line x1="260" y1="-20" x2="480" y2="386" stroke="#1d3568" stroke-width="12"/>
      <line x1="250" y1="-20" x2="470" y2="386" stroke="#3d7bd0" stroke-width="6"/>
      <line x1="470" y1="-20" x2="250" y2="386" stroke="#1d3568" stroke-width="12"/>
      <line x1="480" y1="-20" x2="260" y2="386" stroke="#3d7bd0" stroke-width="6"/>
    </g>
    <rect class="band" x="0" y="44" width="640" height="268" fill="#1b1c1e"/>
  </svg>
  <div class="brand">
    <span class="brand-mark"></span>
    <span class="brand-name">brightvale</span>
  </div>
</section>

<section class="card card-back" aria-label="Card back">
  <svg class="card-art" viewBox="0 0 640 366" aria-hidden="true">
    <g class="stripe-pair">
      <line x1="120" y1="-20" x2="340" y2="386" stroke="#1d3568" stroke-width="12"/>
      <line x1="110" y1="-20" x2="330" y2="386" stroke="#3d7bd0" stroke-width="6"/>
      <line x1="610" y1="-20" x2="390" y2="386" stroke="#1d3568" stroke-width="12"/>
      <line x1="620" y1="-20" x2="400" y2="386" stroke="#3d7bd0" stroke-width="6"/>
    </g>
    <rect class="band" x="0" y="38" width="640" height="286" fill="#1b1c1e"/>
  </svg>

  <div class="brand">
    <span class="brand-mark"></span>
    <span class="brand-name">brightvale</span>
  </div>
  <p class="tagline">Commerce Advancing Methods</p>
  <div class="tagline-rule"></div>

  <div class="contact">
    <p class="contact-name">Martin Coles</p>
    <p class="contact-role">Senior Partner</p>
    <p class="contact-address">48 Harbour Lane West, Suite 1204,<br>Toronto, Ontario, M5J 2K7</p>
    <div class="contact-rule"></div>
    <ul class="contact-list">
      <li>
        <svg class="contact-icon" viewBox="0 0 18 18" aria-label="Office">
          <circle cx="9" cy="9" r="8" fill="none" stroke="#e6e8eb" stroke-width="1"/>
          <path d="M6 5.5l1.5-.5 1 2-1 .8a5 5 0 0 0 2.7 2.7l.8-1 2 1-.5 1.5c-3 .3-6.8-3.5-6.5-6.5z" fill="#e6e8eb"/>
        </svg>
        1 877 555 0143
      </li>
      <li>
        <svg class="contact-icon" viewBox="0 0 18 18" aria-label="Mobile">
          <circle cx="9" cy="9" r="8" fill="none" stroke="#e6e8eb" stroke-width="1"/>
          <rect x="6.5" y="4.5" width="5" height="9" rx="1" fill="none" stroke="#e6e8eb" stroke-width="1"/>
        </svg>
        1 519 555 0172
      </li>
      <li>
        <svg class="contact-icon" viewBox="0 0 18 18" aria-label="Website">
          <circle cx="9" cy="9" r="8" fill="none" stroke="#e6e8eb" stroke-width="1"/>
          <rect x="4.5" y="5.5" width="9" height="6" fill="none" stroke="#e6e8eb" stroke-width="1"/>
          <line x1="7" y1="13.3" x2="11" y2="13.3" stroke="#e6e8eb" stroke-width="1"/>
        </svg>
        www.brightvale.example
      </li>
      <li>
        <svg class="contact-icon" viewBox="0 0 18 18" aria-label="Email">
          <circle cx="9" cy="9" r="8" fill="none" stroke="#e6e8eb" stroke-width="1"/>
          <rect x="4.5" y="6" width="9" height="6" fill="#e6e8eb"/>
          <path d="M4.5 6l4.5 3.5L13.5 6" fill="none" stroke="#1b1c1e" stroke-width="1"/>
        </svg>
        info@brightvale.example
      </li>
    </ul>
    <div class="contact-rule"></div>
  </div>
</section>

</body>
</html>
```